BWP Business Card

A double sided business card based on your "Brindlewood Partners Ltd" Logo. To use the "BWP" logo on 1 side and the full company logo on the reverse.

Detials to be included:

Name: Tomas Wheeler
Postion: Consultant Orthotist & Expert Witness
T: +44 (0) 7700 938271
F: +44 (0) 7654 8820

```html
<!DOCTYPE html>
<html lang="en">
<head>
<meta charset="utf-8">
<title>Brindlewood Partners Ltd – Business Card</title>
<link rel="stylesheet" href="https://fonts.googleapis.com/css2?family=Crimson+Text:wght@400;600&family=Open+Sans:wght@400;700&display=swap">
<style>
  :root {
    --navy: #133e7c;
    --grey: #a3a3a3;
    --ink: #3a3a3a;
    --paper: #ffffff;
    --backdrop: #e6e6ec;
  }
  * { margin: 0; padding: 0; box-sizing: border-box; }
  html, body { width: 1200px; height: 987px; overflow: hidden; }
  body {
    background: var(--backdrop);
    position: relative;
    font-family: "Crimson Text", "Times New Roman", serif;
  }
  .card {
    position: absolute;
    width: 640px;
    height: 366px;
    background: var(--paper);
    border-radius: 22px;
    overflow: hidden;
    box-shadow: 0 6px 18px rgba(0,0,0,.12);
  }
  .card--brand { left: 280px; top: 90px; }
  .card--contact { left: 280px; top: 530px; }

  /* Brand mark: square plus name in the text face */
  .brand-mark {
    position: absolute; left: 60px; top: 146px;
    display: flex; align-items: center; gap: 14px;
  }
  .brand-mark__square { width: 52px; height: 52px; background: var(--navy); }
  .brand-mark__name {
    font-family: "Crimson Text", "Times New Roman", serif;
    font-weight: 600; font-size: 46px; line-height: 1; color: var(--navy);
  }
  .divider { position: absolute; width: 2px; background: var(--grey); }
  .card--brand .divider { left: 262px; top: 108px; height: 150px; }

  /* Brand side company name */
  .company {
    position: absolute; left: 290px; top: 126px; width: 320px;
  }
  .company__name {
    font-family: "Crimson Text", "Times New Roman", serif;
    font-weight: 600; font-size: 34px; line-height: 38px; color: var(--navy);
  }
  .company__tagline {
    margin-top: 12px;
    font-family: "Open Sans", Arial, sans-serif;
    font-weight: 400; font-size: 13px; color: var(--ink);
  }

  /* Contact side */
  .card--contact .brand-mark { left: 40px; top: 44px; }
  .card--contact .brand-mark__square { width: 46px; height: 46px; }
  .card--contact .brand-mark__name { font-size: 40px; }
  .card--contact .divider { left: 300px; top: 34px; height: 124px; }
  .swoosh { position: absolute; inset: 0; }
  .details {
    position: absolute; left: 326px; top: 52px;
    font-size: 19px; line-height: 26px; color: var(--ink);
    list-style: none;
  }
  .details li { display: flex; align-items: center; gap: 8px; }
  .details .address { padding-left: 24px; }
  .details svg { width: 16px; height: 16px; flex: none; fill: var(--navy); }
  .holder {
    position: absolute; left: 34px; top: 282px; color: var(--paper);
    font-family: "Open Sans", Arial, sans-serif;
  }
  .holder__name { font-weight: 700; font-size: 25px; line-height: 30px; }
  .holder__role { font-weight: 400; font-size: 17px; line-height: 24px; }
</style>
</head>
<body>

<section class="card card--brand" aria-label="Business card, brand side">
  <div class="brand-mark">
    <span class="brand-mark__square"></span>
    <span class="brand-mark__name">BWP</span>
  </div>
  <span class="divider"></span>
  <div class="company">
    <div class="company__name">Brindlewood<br>Partners Ltd</div>
    <div class="company__tagline">Excellence in Medical Legal Reporting</div>
  </div>
</section>

<section class="card card--contact" aria-label="Business card, contact side">
  <svg class="swoosh" viewBox="0 0 640 366" aria-hidden="true">
    <path d="M0 96 C180 140 420 210 580 366 L548 366 C400 236 170 170 0 130 Z" fill="var(--grey)"/>
    <path d="M0 140 C170 180 390 240 528 366 L512 366 C380 248 160 190 0 150 Z" fill="var(--navy)"/>
    <path d="M0 160 C160 200 370 252 496 366 L0 366 Z" fill="var(--navy)"/>
  </svg>

  <div class="brand-mark">
    <span class="brand-mark__square"></span>
    <span class="brand-mark__name">BWP</span>
  </div>
  <span class="divider"></span>

  <ul class="details">
    <li class="address">18 Harrowgate Lane Kingston</li>
    <li class="address">Surrey, KT2 4RW</li>
    <li>
      <svg viewBox="0 0 16 16"><path d="M3 1h3l1 4-2 1c1 2 3 4 5 5l1-2 4 1v3c0 1-1 2-2 2C7 15 1 9 1 3c0-1 1-2 2-2z"/></svg>
      +44 (0) 7700 938271
    </li>
    <li>
      <svg viewBox="0 0 16 16"><path d="M4 1h7v4H4zM1 6h14v6h-3v3H4v-3H1zM5 10v4h6v-4z"/></svg>
      +44 (0) 7654 8820
    </li>
    <li>
      <svg viewBox="0 0 16 16"><path d="M1 3h14v10H1zM2 4l6 5 6-5v-.2H2z" fill-rule="evenodd"/></svg>
      tomas@brindlewoodpartners.co.uk
    </li>
  </ul>

  <div class="holder">
    <div class="holder__name">Tomas Wheeler</div>
    <div class="holder__role">Consultant Orthotist &amp; Expert Witness</div>
  </div>
</section>

</body>
</html>
```